Medical Practice needs a Letterhead Design

We need a clean, modern letterhead design for our stem cell medical practice.

Industry/Entity Type

Medical

```html
<!DOCTYPE html>
<html lang="en">
<head>
<meta charset="utf-8">
<title>Halden Regenerative Letterhead</title>
<link href="https://fonts.googleapis.com/css2?family=PT+Sans:wght@400;700&display=swap" rel="stylesheet">
<style>
  :root {
    --backdrop: #5a5a5c;
    --paper: #fbfbfb;
    --ink-dark: #2b3137;
    --ink: #3a3f44;
    --muted: #7b8288;
  }
  * { box-sizing: border-box; margin: 0; padding: 0; }
  html, body {
    width: 1200px; height: 778px; overflow: hidden;
    background: var(--backdrop);
    font-family: "PT Sans", sans-serif;
  }
  .letterhead {
    position: absolute; left: 339px; top: 20px;
    width: 522px; height: 738px;
    background: var(--paper);
    color: var(--ink);
    box-shadow: 0 6px 24px rgba(0,0,0,.35);
  }
  .brand {
    position: absolute; left: 36px; top: 44px;
    font-size: 18px; font-weight: 700; color: var(--ink-dark);
    letter-spacing: .2px; white-space: nowrap;
  }
  .meta {
    position: absolute; left: 36px; top: 124px; width: 100px;
    text-align: right; font-size: 8.5px; line-height: 1.35;
  }
  .meta dt { font-weight: 700; color: var(--ink-dark); }
  .meta dd { margin-bottom: 12px; color: var(--muted); }
  .letter {
    position: absolute; left: 150px; top: 110px; width: 330px;
    font-size: 8.5px; line-height: 1.45;
  }
  .salutation { font-weight: 700; color: var(--ink-dark); margin-bottom: 6px; }
  .letter p { margin-bottom: 9px; }
  .signoff { margin-top: 14px; color: var(--muted); }
  .signature { display: block; margin-top: 6px; width: 70px; height: 26px; }
  .contact {
    position: absolute; left: 36px; bottom: 34px;
    font-size: 6px; line-height: 1.35; color: var(--muted);
  }
  .contact dt { font-weight: 700; color: var(--ink-dark); margin-top: 4px; }
</style>
</head>
<body>
  <main class="letterhead">
    <div class="brand">Halden Regenerative</div>

    <dl class="meta">
      <dt>To</dt><dd>Mauris Euismod</dd>
      <dt>Subject</dt><dd>Egestas Ornare</dd>
      <dt>Date</dt><dd>18.12.2012</dd>
    </dl>

    <article class="letter">
      <p class="salutation">Dear Mauris Euismod,</p>
      <p>Pulla lacinia tellus ac massa imperdiet eu molestie felis euismod. Nullam auctor vulputate dui non scelerisque. Etiam tincidunt erat id elit pulvinar volutpat. Morbi facilisis ultrices egestas. Aenean pellentesque massa vitae lacus mattis dapibus. Nam a nulla eu sapien tempor molestie mattis nec lacus. Vestibulum ante ipsum primis in faucibus orci luctus et ultrices posuere cubilia Curae; Morbi a ultrices sem.</p>
      <p>Morbi consectetur, elit nec egestas ornare, ipsum augue tincidunt ante, ut facilisis augue dolor at risus. Donec adipiscing erat eu massa semper euismod.</p>
      <p>Suspendisse luctus lobortis sagittis. Mauris euismod nibh auctor orci aliquam eleifend quis eu nibh. Nullam condimentum cursus purus, a pulvinar eros adipiscing vitae. Nulla non ligula ac turpis ullamcorper fermentum.</p>
      <p>Praesent mauris ipsum, condimentum a vestibulum vitae, lobortis ut diam. Sed tortor velit, iaculis eu eleifend et, varius eu mauris. Suspendisse et pulvinar est. Pellentesque pharetra libero ut nunc placerat volutpat. Vivamus fringilla ante nec erat consequat aliquet.</p>
      <p>Mauris iaculis mollis tellus eu consectetur. Ut sed elit a tortor tincidunt lacinia eu et leo. Nam nec arcu vitae massa commodo consequat. Vivamus a neque quis nisi scelerisque pretium. Maecenas non orci purus. Morbi tristique nisi vel mi consequat laoreet.</p>
      <p>Pellentesque varius lorem at ante tincidunt fermentum. Fusce sagittis euismod massa, non lacinia risus aliquam eget. Praesent sit amet orci non augue semper ullamcorper. Aenean in mi eros. Proin mattis sapien sit amet arcu tempus posuere.</p>
      <p>Aliquam mattis magna sit amet mi posuere elementum. Cum sociis natoque penatibus et magnis dis parturient montes, nascetur ridiculus mu</p>
      <p class="signoff">Daniel Marsh</p>
      <svg class="signature" role="img" aria-label="Handwritten signature of Daniel Marsh" viewBox="0 0 70 26">
        <rect width="70" height="26" rx="3" fill="#e6e8ea"/>
      </svg>
    </article>

    <dl class="contact">
      <dt>ADDRESS</dt>
      <dd>12 Harbor Lane</dd>
      <dd>Suite 4, Westbrook</dd>
      <dt>PHONE</dt>
      <dd>555 010 2244</dd>
      <dt>EMAIL &amp; WEB</dt>
      <dd>info@halden.example</dd>
      <dd>halden.example</dd>
    </dl>
  </main>
</body>
</html>
```